Investment Advisor E-Newsletter Banner Design

I need a banner designed for an email newsletter that will be sent monthly to clients and prospects. We want to see designs that are elegant and use our logo well. The banner should be 922x150px and should go well with the www.tlvbanda.com website. Should include Logo and email and phone number.

Target Market(s)

High net worth investors

Number of Pages Required

1 page

Requirements
Must have
• logo, place for email (info@tlvbanda.com) and phone number (415-297-6180), colors and design that work well with www.tlvbanda.com website

```html
<!DOCTYPE html>
<html lang="en">
<head>
<meta charset="utf-8">
<title>Telva Banda Capital – Newsletter Banner</title>
<link rel="stylesheet" href="https://fonts.googleapis.com/css2?family=Cormorant+Garamond:ital,wght@0,500;1,500&display=swap">
<style>
  :root {
    --navy-light: #2f2f8c;
    --navy-dark: #1c1c5a;
    --ink: #1f1f5c;
    --band-black: #1a1a1a;
    --white: #ffffff;
    --window-bright: #eef2f6;
    --window-soft: #c7d3df;
    --office-mid: #8c9db0;
    --suit-dark: #39424f;
    --suit-navy: #2a3140;
  }
  html, body {
    margin: 0;
    padding: 0;
    width: 1200px;
    height: 195px;
    overflow: hidden;
    background: var(--white);
  }
  .banner {
    display: block;
    width: 1200px;
    height: 195px;
  }
  .brand-name {
    font-family: "Cormorant Garamond", Georgia, serif;
    font-weight: 500;
    font-size: 31px;
    fill: var(--white);
  }
  .contact-text {
    font-family: "Cormorant Garamond", Georgia, serif;
    font-style: italic;
    font-weight: 500;
    font-size: 19px;
  }
  .contact-email { fill: var(--ink); }
  .contact-phone { fill: var(--white); }
</style>
</head>
<body>
<svg class="banner" viewBox="0 0 922 150" width="1200" height="195" xmlns="http://www.w3.org/2000/svg">
  <defs>
    <linearGradient id="navyFill" x1="0" y1="0" x2="1" y2="1">
      <stop offset="0" stop-color="var(--navy-light)"/>
      <stop offset="1" stop-color="var(--navy-dark)"/>
    </linearGradient>
    <linearGradient id="officeLight" x1="0" y1="0" x2="1" y2="0">
      <stop offset="0" stop-color="var(--office-mid)"/>
      <stop offset="0.3" stop-color="var(--window-soft)"/>
      <stop offset="0.7" stop-color="var(--window-bright)"/>
      <stop offset="1" stop-color="var(--window-soft)"/>
    </linearGradient>
    <linearGradient id="officeDepth" x1="0" y1="0" x2="0" y2="1">
      <stop offset="0" stop-color="var(--suit-navy)" stop-opacity="0"/>
      <stop offset="0.45" stop-color="var(--suit-navy)" stop-opacity="0.25"/>
      <stop offset="1" stop-color="var(--suit-dark)" stop-opacity="0.85"/>
    </linearGradient>
    <clipPath id="photoClip">
      <path d="M0 0 H430 C405 40 392 80 380 108 C368 130 350 143 332 150 H0 Z"/>
    </clipPath>
  </defs>

  <!-- Header photo area -->
  <g class="hero-photo" role="img" aria-label="Photo of three business professionals reviewing documents in a bright glass office" clip-path="url(#photoClip)">
    <rect x="0" y="0" width="440" height="150" fill="url(#officeLight)"/>
    <rect x="0" y="0" width="440" height="150" fill="url(#officeDepth)"/>
  </g>

  <!-- Navy brand panel -->
  <path class="brand-panel" d="M442 0 H922 V110 H392 C412 72 428 32 442 0 Z" fill="url(#navyFill)"/>

  <!-- Phone band -->
  <path class="phone-band" d="M684 110 H922 V150 H656 Z" fill="var(--band-black)"/>

  <!-- Brand name -->
  <g class="brand">
    <circle cx="582" cy="49" r="20" fill="var(--white)"/>
    <text class="brand-name" x="614" y="59">Telva Banda Capital</text>
  </g>

  <!-- Email -->
  <g class="contact contact-email-group">
    <circle cx="420" cy="128" r="13" fill="var(--navy-light)"/>
    <rect x="413" y="123" width="14" height="10" rx="1" fill="var(--white)"/>
    <path d="M413 123.5 L420 129 L427 123.5" fill="none" stroke="var(--navy-light)" stroke-width="1.2"/>
    <text class="contact-text contact-email" x="452" y="134">info@tlvbanda.com</text>
  </g>

  <!-- Phone -->
  <g class="contact contact-phone-group">
    <circle cx="716" cy="128" r="13" fill="var(--white)"/>
    <path d="M711.5 121.5 c1-1 2-1 2.6 0 l1.4 2.3 c.5.8.3 1.6-.4 2.1 l-.8.6 c.7 1.6 2 2.9 3.6 3.6 l.6-.8 c.5-.7 1.3-.9 2.1-.4 l2.3 1.4 c1 .6 1 1.6 0 2.6 l-.9.9 c-1.2 1.2-3.5.9-6.4-1.3 c-2.2-1.7-3.9-3.6-4.9-5.6 c-1.1-2.2-1.1-3.9-.1-4.9 Z"
          fill="var(--band-black)"/>
    <text class="contact-text contact-phone" x="763" y="134">415-297-6180</text>
  </g>
</svg>
</body>
</html>
```